BRAND BOOK design

We are a new swimwear brand. We have a vague idea of what we want. We have some colors we would like to use. We would love someone who can provide simple, sophisticated yet an edgy design for our first brand book. The brand book will contain our campaign photos and you will have to come up with layouts and simple designs to insert these photos and short quotes or descriptions. The brand book will contain our brand identity and express the vibes we want our customers to feel get from our brand.

Target Market(s)

US and Australia

Industry/Entity Type

Fashion

Font styles to use
Other font styles liked:
• Futura Medium

Colors
f9d9e8
cfcfcf
ffffff

Requirements
Must have
• simple modern layout with pop elements.
• photos must be placed with enough space.
• also need minimal space for words.
Nice to have
• Simple layouts that aren't common. Designs that can show our identity.
• Please refer to our website (under construction): www.velmorantiquell.com
Should not have
• mere copies of other brand designs

```html
<!DOCTYPE html>
<html lang="en">
<head>
<meta charset="utf-8">
<title>Brand Book — Spreads 09–12</title>
<link rel="stylesheet" href="https://fonts.googleapis.com/css2?family=Jost:wght@300;400&family=Courier+Prime&display=swap">
<style>
  :root {
    --board: #1b1b1b;
    --page: #ffffff;
    --ink: #555555;
    --rule: #cfcfcf;
    --label: #33e633;
    --photo-garden: linear-gradient(160deg, #6f8a4a 0%, #7d8d96 40%, #9aa3a8 65%, #c9a58a 100%);
    --photo-sewing: linear-gradient(135deg, #d9d4d2 0%, #c7bcb6 45%, #f1e6cf 75%, #bfb4a8 100%);
    --photo-garment: linear-gradient(160deg, #d4d8de 0%, #c2c7cf 100%);
    --photo-pool: linear-gradient(180deg, #2f5c93 0%, #6e8fae 35%, #e7d0c2 70%, #2c3a4a 100%);
  }
  * { margin: 0; padding: 0; box-sizing: border-box; }
  html, body { width: 1200px; height: 1200px; overflow: hidden; background: var(--board); }
  body { position: relative; font-family: "Jost", "Futura", sans-serif; font-weight: 300; color: var(--ink); }

  .spread { position: absolute; width: 564px; height: 355px; background: var(--page); overflow: hidden; }
  .spread--09 { left: 24px; top: 128px; }
  .spread--10 { left: 612px; top: 128px; }
  .spread--11 { left: 24px; top: 716px; }
  .spread--12 { left: 612px; top: 716px; }

  .photo { position: absolute; }
  .caption { position: absolute; white-space: nowrap; letter-spacing: -0.2px; }

  .spread--09 .photo { left: 29px; top: 0; width: 236px; height: 355px; background: var(--photo-garden); }
  .spread--09 .caption { left: 298px; top: 302px; font-size: 21px; }

  .spread--10 .bracket { position: absolute; left: 20px; top: 20px; width: 28px; height: 30px; border-top: 1px solid var(--ink); border-left: 1px solid var(--ink); }
  .spread--10 .headline { position: absolute; left: 37px; top: 29px; font-size: 27px; white-space: nowrap; letter-spacing: -0.3px; }
  .spread--10 .photo { left: 0; top: 84px; width: 334px; height: 222px; background: var(--photo-sewing); }
  .spread--10 .caption { left: 346px; top: 276px; font-size: 21px; }

  .spread--11 .statement { position: absolute; left: 31px; top: 36px; width: 178px; height: 110px; border: 1px solid var(--rule); padding: 10px 0 0 16px; font-size: 21px; line-height: 32px; }
  .spread--11 .photo { left: 260px; top: 32px; width: 232px; height: 298px; background: var(--photo-garment); border-radius: 40px 40px 90px 20px; }

  .spread--12 .photo { left: 37px; top: 0; width: 236px; height: 355px; background: var(--photo-pool); }
  .spread--12 .caption { left: 308px; top: 128px; font-size: 21px; line-height: 32px; }

  .file-label { position: absolute; font-family: "Courier Prime", monospace; font-size: 9px; color: var(--label); transform: translateX(-50%); }
</style>
</head>
<body>
  <section class="spread spread--09">
    <div class="photo" role="img" aria-label="Campaign photo: model in a coral strappy bandeau bikini kneeling on cushions by a garden wall"></div>
    <p class="caption">FOR THE WILD AND FREE</p>
  </section>

  <section class="spread spread--10">
    <span class="bracket"></span>
    <h2 class="headline">WE STRIVE FOR QUALITY AND DETAILS</h2>
    <div class="photo" role="img" aria-label="Close-up photo of hands guiding fabric under a sewing machine needle"></div>
    <p class="caption">CRAFTMANSHIP</p>
  </section>

  <section class="spread spread--11">
    <p class="statement">ORIGINAL and<br>HANDCRAFTED<br>with LOVE</p>
    <div class="photo" role="img" aria-label="Product photo: grey one-piece swimsuit with strappy open back, laid flat"></div>
  </section>

  <section class="spread spread--12">
    <div class="photo" role="img" aria-label="Campaign photo: model in a white hat and white strappy-back one-piece swimsuit by a pool"></div>
    <p class="caption">FLATTERING CUTS,<br>MAXIMIZING COMFORT</p>
  </section>

  <span class="file-label" style="left:309px; top:589px;">09.png</span>
  <span class="file-label" style="left:897px; top:589px;">10.png</span>
  <span class="file-label" style="left:309px; top:1177px;">11.png</span>
  <span class="file-label" style="left:897px; top:1177px;">12.png</span>
</body>
</html>
```